Webdesign für Hersteller für Pack- und Palettieranlagen für den Getränke- und Lebensmittelbereich
Webdesign für Hersteller für Pack- und Palettieranlagen für den Getränke- und Lebensmittelbere..
Zielgruppe
Hersteller für Pack- und Palettieranlagen für den Getränke- und Lebensmittelbereich
Zielgruppe: Getränke- und Lebensmittelhersteller
Aufgabenstellung
die zukünftige Seite soll dynamischer und intuitiver werden
klare Strukturen, aber morderner als das jetztige Layout
Keine Kopie der alten Seite www.kolmatech.de!
Startseite soll aufgeräumter sein
Logo, Rufnummer, Mail, Social Media
Startseite mit großem Headerbild (Slider)

```html
<!DOCTYPE html>
<html lang="de">
<head>
<meta charset="utf-8">
<title>Kolmatech Maschinenbau GmbH – Startseite</title>
<link href="https://fonts.googleapis.com/css2?family=Poppins:wght@400;500;600;700&display=swap" rel="stylesheet">
<style>
:root{
  --green:#5ea821;
  --green-dark:#3e8a10;
  --green-light:#79c13a;
  --white:#ffffff;
  --ink:#3a3a3a;
  --muted:#6b6b6b;
  --line:#e6e6e6;
}
*{box-sizing:border-box;margin:0;padding:0}
html,body{width:960px;height:1200px;overflow:hidden;background:var(--white)}
body{font-family:"Poppins",sans-serif;color:var(--ink)}
.page{width:960px;height:1200px;overflow:hidden;position:relative}

/* header */
.topbar{height:68px;display:flex;align-items:center;justify-content:space-between;padding:0 48px;background:var(--white)}
.brand{display:flex;align-items:center;gap:10px}
.brand-dot{width:22px;height:22px;border-radius:50%;background:var(--green)}
.brand-text{display:flex;flex-direction:column;line-height:1}
.brand-name{font-weight:700;font-size:24px;color:var(--green);letter-spacing:.5px}
.brand-sub{font-size:10px;color:var(--muted);margin-top:3px}
.contact{display:flex;align-items:center;gap:18px;font-size:12px;color:var(--green-dark)}
.contact-item{display:flex;align-items:center;gap:6px}
.contact-icon{width:22px;height:22px;border-radius:50%;background:var(--green);display:flex;align-items:center;justify-content:center}
.social{display:flex;gap:6px}
.social span{width:20px;height:20px;border-radius:50%;background:var(--green)}

.mainnav{height:34px;background:var(--green);display:flex;align-items:center;gap:26px;padding:0 48px}
.mainnav a{color:var(--white);font-size:12px;text-decoration:none;font-weight:500}

/* hero */
.hero{position:relative;height:500px;background:linear-gradient(180deg,var(--green) 0%,var(--green-dark) 100%);overflow:hidden}
.hero-photo{position:absolute;left:0;right:48px;top:0;bottom:20px;
  background:linear-gradient(180deg,rgba(255,255,255,0) 40%,var(--green) 92%),
  linear-gradient(100deg,#b9d7a8 0%,#8fbf86 35%,#4d7f66 60%,#3c6470 80%,#9bb6ab 100%)}
.hero-content{position:absolute;left:0;right:48px;bottom:58px;text-align:center;color:var(--white)}
.hero-title{font-size:36px;font-weight:600;margin-bottom:12px}
.hero-lead{font-size:13px;line-height:1.5;margin-bottom:22px}
.hero-actions{display:flex;justify-content:center;gap:16px}
.btn{display:inline-block;font-size:13px;font-weight:500;padding:11px 26px;border:1.5px solid var(--white);text-decoration:none}
.btn-solid{background:var(--white);color:var(--green-dark)}
.btn-ghost{color:var(--white)}
.slider-dots{position:absolute;right:64px;bottom:70px;display:flex;flex-direction:column;gap:6px}
.slider-dots span{width:6px;height:6px;border-radius:50%;background:rgba(255,255,255,.55)}
.slider-dots span.active{background:var(--white)}

/* about */
.about{background:linear-gradient(180deg,var(--green-dark),var(--green));color:var(--white);padding:60px 48px 56px;display:grid;grid-template-columns:1fr 1fr;gap:48px}
.eyebrow{font-size:10px;font-weight:600;letter-spacing:.5px;margin-bottom:12px}
.about-title{font-size:21px;font-weight:600;line-height:1.25;margin-bottom:26px}
.btn-small{font-size:11px;padding:7px 18px;border:1.5px solid var(--white);color:var(--white);text-decoration:none;display:inline-block}
.about-text p{font-size:11px;line-height:1.6;margin-bottom:10px}
.about-photo{height:150px;margin-top:16px;background:linear-gradient(120deg,#6b6f5a,#a39a74 40%,#4f6a8b 75%,#8a8e80)}

/* products */
.products{padding:52px 48px;display:grid;grid-template-columns:1fr 1fr;gap:48px;color:var(--green-dark)}
.products .eyebrow{color:var(--green-dark)}
.products-title{font-size:21px;font-weight:600;line-height:1.25;margin-bottom:26px}
.btn-outline{font-size:11px;padding:7px 18px;border:1.5px solid var(--green);color:var(--green-dark);text-decoration:none;display:inline-block}
.product-name{font-size:15px;font-weight:600;margin-bottom:10px}
.product-photo{height:170px;background:linear-gradient(120deg,#2f6b46,#6fa37b 45%,#c9d7cd 70%,#3f5c4f)}
</style>
</head>
<body>
<div class="page">

  <header class="topbar">
    <div class="brand">
      <span class="brand-dot"></span>
      <div class="brand-text">
        <span class="brand-name">KOLMATECH</span>
        <span class="brand-sub">Maschinenbau GmbH</span>
      </div>
    </div>
    <div class="contact">
      <div class="contact-item">
        <span class="contact-icon">
          <svg width="12" height="12" viewBox="0 0 24 24"><path fill="#fff" d="M6.6 10.8a15.2 15.2 0 0 0 6.6 6.6l2.2-2.2a1 1 0 0 1 1-.25 11.4 11.4 0 0 0 3.6.57 1 1 0 0 1 1 1V20a1 1 0 0 1-1 1A17 17 0 0 1 3 4a1 1 0 0 1 1-1h3.5a1 1 0 0 1 1 1c0 1.25.2 2.45.57 3.57a1 1 0 0 1-.25 1z"/></svg>
        </span>
        03 4567 / 890 - 0
      </div>
      <div class="contact-item">
        <span class="contact-icon">
          <svg width="12" height="12" viewBox="0 0 24 24"><rect x="3" y="6" width="18" height="12" rx="1.5" fill="#fff"/><path d="M3.5 6.5 12 13l8.5-6.5" stroke="#5ea821" stroke-width="1.8" fill="none"/></svg>
        </span>
        info@kolmatech.de
      </div>
      <div class="social" aria-label="Soziale Netzwerke">
        <span></span><span></span><span></span><span></span>
      </div>
    </div>
  </header>

  <nav class="mainnav">
    <a href="#">Unternehmen</a>
    <a href="#">Jobs &amp; Karriere</a>
    <a href="#">Palettiertechnik</a>
    <a href="#">Packertechnik</a>
    <a href="#">Fördertechnik</a>
    <a href="#">Anlagen</a>
    <a href="#">Gebrauchtmaschinen</a>
    <a href="#">Aktuelles</a>
    <a href="#">Kontakt</a>
  </nav>

  <section class="hero">
    <div class="hero-photo" role="img" aria-label="Foto: lächelnder Techniker mit Schutzhelm und Schutzbrille in der Produktionshalle"></div>
    <div class="hero-content">
      <h1 class="hero-title">Tauchen Sie ein in die Welt von Kolmatech</h1>
      <p class="hero-lead">Bei uns trifft Tradition auf Innovation. Wir planen und konstruieren für Sie<br>maßgeschneiderte Lösungen für Ihre Produktionsanlagen.</p>
      <div class="hero-actions">
        <a class="btn btn-solid" href="#">Mehr Informationen</a>
        <a class="btn btn-ghost" href="#">Kontakt aufnehmen</a>
      </div>
    </div>
    <div class="slider-dots"><span></span><span></span><span class="active"></span></div>
  </section>

  <section class="about">
    <div>
      <div class="eyebrow">ÜBER UNS</div>
      <h2 class="about-title">Das traditionsreiche Familienunternehmen Kolmatech plant, entwickelt und baut Pack- und Palettieranlagen für den Getränke- und Lebensmittelbereich.</h2>
      <a class="btn-small" href="#">Mehr über uns</a>
    </div>
    <div class="about-text">
      <p>Wir sind ein Unternehmen mit einer über hundertjährigen Geschichte. Gegründet als kleine Schmiede, wird die Firma heute in vierter Generation weitergeführt und mit viel persönlichem Engagement ausgebaut.</p>
      <p>Unsere Fertigung bietet viel Raum für moderne Technik. Dadurch stehen unseren Kunden beste Voraussetzungen zur Verfügung, um Aufgaben optimal zu lösen.</p>
      <p>Mit einer hohen Fertigungstiefe stellen wir Förder- und Verpackungstechnik von der einzelnen Maschine bis zur kompletten Anlage her.</p>
      <div class="about-photo" role="img" aria-label="Foto: drei Mitarbeiter in Arbeitskleidung in der Werkhalle"></div>
    </div>
  </section>

  <section class="products">
    <div>
      <div class="eyebrow">PRODUKTE</div>
      <h2 class="products-title">Mit Erfahrung und Know-how planen und konstruieren wir moderne und effiziente Anlagen, die optimal auf die Bedürfnisse unserer Kunden abgestimmt sind.</h2>
      <a class="btn-outline" href="#">Mehr Informationen</a>
    </div>
    <div>
      <h3 class="product-name">Palettiertechnik</h3>
      <div class="product-photo" role="img" aria-label="Foto: grüne Palettieranlage in einer Produktionshalle"></div>
    </div>
  </section>

</div>
</body>
</html>
```